Sci Fi/ Secret Agent Author needs website design!

My name is Lark Whitby and I am an author. I require a site that can provide information about myself and my books and other works.

I would like it to have a Home, blog function, (about the) books/series section so people can visit another section and read about each individual book that's going to be released. A resources page, a Store, social media links and ability to load/embed videos from clipvane and other.

I write mild scifi/thriller/conspiracy/secret government type novels. -At the moment-. The series follows a strong female lead that is an agent with a secret organisation in a classified military installation.

The theme would be professional yet possibly show this element.

/military fiction/thriller/fantasy/Sci fi/ femme-fatal, readers. Mostly females, age 18-60
Novel readers

5+ page

• Would like designers to follow brief. :)
• My budget includes all the pages I will need;
• eg home, blog, resources, store, ability to pay with coinpouch and Credit Cards
• , ability to have trailers from clipvane etc. Must have links to the social media mentioned in the brief.
• use of the colours I have suggested. electric/indigo purple, fuschia highlights , dark greys
• as I will possibly base branding for social media ETC on the look of your website design and colour scheme.
• Ability for trailer on front page??
• Should not be too cluttered. (But I am open to all ideas)

```html
<!DOCTYPE html>
<html lang="en">
<head>
<meta charset="utf-8">
<title>Lark Whitby – Author</title>
<link rel="stylesheet" href="https://fonts.googleapis.com/css2?family=Montserrat:wght@400;600;700&family=Open+Sans:wght@400;600&display=swap">
<style>
:root{
  --purple:#6a1bb8;
  --purple-dark:#4b0e8a;
  --fuchsia:#c21ccf;
  --ink:#2b2b2b;
  --grey:#6d6d6d;
  --light:#f3f3f3;
  --hero-a:#1e1a2a;
  --hero-b:#4a4055;
}
*{margin:0;padding:0;box-sizing:border-box}
html,body{width:729px;height:1200px;overflow:hidden;background:#fff}
body{font-family:"Open Sans",Arial,sans-serif;color:var(--ink);position:relative}
.site-header{height:53px;display:flex;align-items:center;justify-content:space-between;padding:0 32px 0 22px}
.brand{font-family:"Montserrat",sans-serif;font-weight:700;font-size:28px;color:var(--purple);letter-spacing:.5px}
.social-top{display:flex;gap:5px;align-items:center}
.social-top span{width:14px;height:14px;border:1px solid #bbb;border-radius:50%}
.social-top .cart{width:20px;height:20px;background:#111;border:none;margin-left:6px;position:relative}
.social-top .cart::after{content:"";position:absolute;right:-3px;top:-3px;width:8px;height:8px;border-radius:50%;background:var(--fuchsia)}
.main-nav{height:25px;background:var(--purple);display:flex;align-items:center;padding:0 22px;font-family:"Montserrat",sans-serif;font-size:8px;font-weight:600;color:#fff;text-transform:uppercase}
.main-nav a{color:#fff;text-decoration:none;padding:0 11px;height:25px;line-height:25px}
.main-nav a.active{background:var(--purple-dark)}
.main-nav .search{margin-left:auto;width:15px;height:15px;border:1px solid #fff;border-radius:50%;display:flex;align-items:center;justify-content:center}
.hero{position:relative;height:287px;background:radial-gradient(ellipse at 50% 55%,var(--hero-b),var(--hero-a) 75%);display:flex;flex-direction:column;align-items:center;justify-content:center;color:#fff}
.play{width:34px;height:34px;border-radius:50%;background:var(--purple);display:flex;align-items:center;justify-content:center;margin-top:-40px}
.hero h1{font-family:"Montserrat",sans-serif;font-size:20px;font-weight:600;margin-top:56px}
.hero p{font-size:10px;opacity:.9;margin-top:2px}
.arrow{position:absolute;top:138px;width:10px;height:14px;background:rgba(0,0,0,.5)}
.arrow.l{left:0}.arrow.r{right:0}
.welcome{position:relative;height:410px;background:linear-gradient(90deg,#fbfbfb 0,#ececec 40%,#d6d6d6 100%);overflow:hidden}
.welcome .shadow-art{position:absolute;left:250px;top:0;width:479px;height:410px;background:
  radial-gradient(ellipse 38% 42% at 68% 42%,#4e4e4e,#8a8a8a 40%,rgba(190,190,190,0) 100%),
  radial-gradient(ellipse 20% 30% at 35% 40%,rgba(110,110,110,.55),rgba(200,200,200,0) 100%)}
.welcome-text{position:absolute;left:80px;top:38px;width:320px}
.welcome h2{font-family:"Montserrat",sans-serif;font-size:20px;color:var(--purple);font-weight:700}
.welcome .rule{width:40px;height:2px;background:var(--fuchsia);margin:4px 0 10px}
.welcome p{font-size:6.6px;line-height:10px;color:var(--grey);margin-bottom:10px}
.portrait{position:absolute;left:80px;top:218px;width:98px;height:122px;background:linear-gradient(#f5f1ea,#d9c9a8 60%,#4b3c9a)}
.books{text-align:center;padding-top:14px}
.books h2{font-family:"Montserrat",sans-serif;font-size:18px;color:var(--purple);font-weight:700}
.books .rule{width:40px;height:2px;background:var(--fuchsia);margin:4px auto 18px}
.book-grid{display:flex;gap:13px;justify-content:center}
.book{width:133px}
.cover{height:171px}
.book p{font-size:8.5px;margin-top:9px;text-align:left}
.c1{background:linear-gradient(#3a5160,#7d93a0)}
.c2{background:linear-gradient(#0a0a0a,#5a5a5a)}
.c3{background:linear-gradient(#15303a,#2a4b58)}
.c4{background:linear-gradient(#101418,#2e3a44)}
.newsletter{position:absolute;left:78px;top:1064px;width:573px;height:34px;display:flex}
.newsletter .field{flex:1;background:var(--purple);color:#e6d7f5;font-size:8px;display:flex;align-items:center;padding-left:12px}
.newsletter .btn{width:190px;background:var(--purple-dark);color:#fff;font-family:"Montserrat",sans-serif;font-weight:700;font-size:11px;display:flex;align-items:center;justify-content:center;gap:6px}
.footer-links{position:absolute;top:1118px;left:0;width:729px;text-align:center;font-size:6.5px;color:var(--grey)}
.footer-links a{color:var(--grey);text-decoration:none;padding:0 4px}
.copyright{position:absolute;top:1136px;left:0;width:729px;text-align:center;font-size:6px;color:var(--grey)}
.social-bar{position:absolute;left:0;bottom:0;width:729px;height:34px;display:flex}
.social-bar span{flex:1;color:#fff;font-size:8px;font-weight:600;display:flex;align-items:center;justify-content:center}
</style>
</head>
<body>
<header class="site-header">
  <div class="brand">Lark Whitby</div>
  <div class="social-top"><span></span><span></span><span></span><span></span><span></span><span class="cart"></span></div>
</header>
<nav class="main-nav">
  <a class="active">Home</a><a>About the book</a><a>Resources</a><a>Store</a><a>Blog</a><a>Contact us</a>
  <span class="search"><svg width="7" height="7" viewBox="0 0 10 10"><circle cx="4" cy="4" r="3" fill="none" stroke="#fff" stroke-width="1.5"/><line x1="6.3" y1="6.3" x2="9.5" y2="9.5" stroke="#fff" stroke-width="1.5"/></svg></span>
</nav>
<section class="hero" role="img" aria-label="Woman reading a glowing book among dark library shelves">
  <div class="play"><svg width="12" height="14" viewBox="0 0 12 14"><path d="M2 1l9 6-9 6z" fill="#fff"/></svg></div>
  <h1>INTEGER SODALES</h1>
  <p>Nulla non dolor ut lorem tempor maximus</p>
  <span class="arrow l"></span><span class="arrow r"></span>
</section>
<section class="welcome">
  <div class="shadow-art" role="img" aria-label="Shadowy figure pressing hands against frosted glass"></div>
  <div class="welcome-text">
    <h2>WELCOME</h2>
    <div class="rule"></div>
    <p>Lorem ipsum dolor sit amet, consectetur adipiscing elit. Integer sodales ullamcorper nisi, vitae tempor magna feugiat at. Donec varius mauris sed lectus viverra, eget finibus neque facilisis. Curabitur a turpis nec ipsum porta luctus. Maecenas quis nunc vel velit pretium hendrerit sed in ligula. Vivamus pulvinar efficitur lacus, a dictum tortor sagittis id. Sed facilisis tellus eu leo dapibus blandit. Nunc posuere risus vitae mauris cursus, in tempor orci vehicula. Praesent auctor lorem ut quam ultricies, et cursus ante pharetra. Morbi ac metus non augue feugiat ornare.</p>
    <p>Proin sodales eros quis justo scelerisque, in porttitor nibh dictum. Nam fermentum velit non arcu rhoncus, ac aliquet lectus tincidunt. Aenean vitae ante id risus interdum commodo. Suspendisse potenti. Etiam a odio non sem volutpat gravida at vel orci. Fusce luctus magna sed turpis egestas, nec pulvinar nibh volutpat. Integer blandit leo in sapien bibendum, quis laoreet massa convallis. Duis iaculis diam eget mi sodales malesuada. Cras tincidunt sem vitae neque facilisis porta.</p>
  </div>
  <div class="portrait" role="img" aria-label="Author portrait photo"></div>
</section>
<section class="books">
  <h2>BOOKS</h2>
  <div class="rule"></div>
  <div class="book-grid">
    <div class="book"><div class="cover c1" role="img" aria-label="Book cover: woman seated in misty blue light"></div><p>Integer sodales ullamcorper</p></div>
    <div class="book"><div class="cover c2" role="img" aria-label="Book cover: figure walking into a light beam"></div><p>Integer sodales ullamcorper</p></div>
    <div class="book"><div class="cover c3" role="img" aria-label="Book cover: woman in dark dress in a forest"></div><p>Integer sodales ullamcorper</p></div>
    <div class="book"><div class="cover c4" role="img" aria-label="Book cover: hooded figure in shadow"></div><p>Integer sodales ullamcorper</p></div>
  </div>
</section>
<form class="newsletter">
  <div class="field">Enter your Email for Newsletter Subscribe</div>
  <div class="btn"><svg width="11" height="8" viewBox="0 0 11 8"><rect width="11" height="8" fill="#fff"/><path d="M0 0l5.5 4.5L11 0" fill="none" stroke="#4b0e8a"/></svg>SUBSCRIBE</div>
</form>
<div class="footer-links"><a>Home</a>|<a>About the book</a>|<a>Resources</a>|<a>Store</a>|<a>Blog</a>|<a>Contact us</a></div>
<div class="copyright">Copyright © 2017 Lark Whitby . All rights reserved.</div>
<footer class="social-bar">
  <span style="background:#3b5998">Friendwall</span>
  <span style="background:#1da1f2">Chirper</span>
  <span style="background:#dd4b39">Circlenet</span>
  <span style="background:#cb2027">Pinboard</span>
  <span style="background:#0e76a8">Linkpost</span>
  <span style="background:#517fa4">Snapframe</span>
</footer>
</body>
</html>
```